Awesome business card design needed

We need a new business card design to go with our new logo.
We are a web development agency that specialises in highly complex back-end integrations as opposed to design, our customers are retailers, hotels, hospitals and any other organisation that has a large online marketing department.
Take a look at our website - www.brenoloft.com for some inspiration.
We want our new business cards to exude class, professionalism and style.
We are likely to choose a high-end card to print them on but we want the design of the card itself to really turn heads.
We have no specific colour requirements, the logo as you will see is a turquoise colour R89 G171 B167 #59aba7 but it can also be in white if you want to make the colour of the card something different.
The information on the card should be:
Name
Position
Tel
email
Potentially a double sided card could have our web address, twitter and FB links.

```html
<!DOCTYPE html>
<html lang="en">
<head>
<meta charset="utf-8">
<title>Brenoloft Business Card</title>
<link rel="stylesheet" href="https://fonts.googleapis.com/css2?family=Lato:wght@400;700&display=swap">
<style>
  :root {
    --teal: #59aba7;
    --white: #ffffff;
    --ink: #3a3a3a;
    --backdrop: #eeeeec;
    --card-shadow: rgba(0, 0, 0, 0.12);
  }
  * { box-sizing: border-box; margin: 0; padding: 0; }
  html, body {
    width: 1200px;
    height: 720px;
    overflow: hidden;
    background: var(--backdrop);
    font-family: "Lato", sans-serif;
  }
  .canvas {
    position: relative;
    width: 1200px;
    height: 720px;
    display: flex;
    align-items: center;
    justify-content: center;
    gap: 40px;
  }
  .card {
    position: relative;
    width: 540px;
    height: 309px;
    overflow: hidden;
    box-shadow: 0 6px 18px var(--card-shadow);
  }

  /* Front side */
  .card-front { background: var(--white); }
  .card-front .brand-area {
    height: 176px;
    display: flex;
    flex-direction: column;
    align-items: center;
    justify-content: flex-end;
    padding-bottom: 14px;
  }
  .card-front .wordmark {
    color: var(--teal);
    font-weight: 700;
    font-size: 64px;
    letter-spacing: 2px;
    line-height: 1;
  }
  .card-front .address {
    margin-top: 16px;
    font-size: 11px;
    color: var(--ink);
    letter-spacing: 0.3px;
  }
  .card-front .contact-band {
    position: absolute;
    left: 0; right: 0; bottom: 0;
    height: 133px;
    background: var(--teal);
    color: var(--white);
    padding: 16px 28px;
  }
  .contact-band .name {
    font-size: 15px;
    font-weight: 700;
    letter-spacing: 0.5px;
  }
  .contact-band .name .position {
    font-weight: 400;
    font-size: 12px;
  }
  .contact-list {
    list-style: none;
    margin-top: 10px;
  }
  .contact-list li {
    display: flex;
    align-items: center;
    gap: 10px;
    font-size: 12.5px;
    line-height: 1;
    margin-bottom: 9px;
  }
  .contact-list svg { width: 11px; height: 11px; flex: none; }

  /* Back side */
  .card-back {
    background: var(--teal);
    color: var(--white);
    display: flex;
    flex-direction: column;
    align-items: center;
    justify-content: center;
  }
  .card-back .wordmark {
    font-weight: 700;
    font-size: 84px;
    letter-spacing: 3px;
    line-height: 1;
  }
  .card-back .follow {
    display: flex;
    align-items: center;
    gap: 8px;
    margin-top: 22px;
    font-size: 15px;
    letter-spacing: 0.4px;
  }
  .social-dot {
    width: 22px;
    height: 22px;
    border-radius: 50%;
    background: var(--white);
  }
  .card-back .web {
    margin-top: 12px;
    font-size: 15px;
    letter-spacing: 1.5px;
  }
</style>
</head>
<body>
<main class="canvas">
  <section class="card card-front" aria-label="Business card front">
    <div class="brand-area">
      <div class="wordmark">brenoloft</div>
      <p class="address">Street Name, City Name, State Zip Code</p>
    </div>
    <div class="contact-band">
      <p class="name">YOUR NAME, <span class="position">POSITION</span></p>
      <ul class="contact-list">
        <li>
          <svg viewBox="0 0 12 12" aria-hidden="true"><circle cx="6" cy="6" r="5.2" fill="none" stroke="#fff" stroke-width="1"/><path d="M4 3.5 L5 3.5 L5.5 5 L4.8 5.6 Q5.6 7 6.6 7.4 L7.2 6.7 L8.6 7.2 L8.6 8.2 Q5 8.4 3.8 4.4 Z" fill="#fff"/></svg>
          <span>123-456-7890</span>
        </li>
        <li>
          <svg viewBox="0 0 12 12" aria-hidden="true"><rect x="1" y="3" width="10" height="7" fill="none" stroke="#fff" stroke-width="1.2"/><path d="M1 3 L6 7 L11 3" fill="none" stroke="#fff" stroke-width="1.2"/></svg>
          <span>info@brenoloft.com</span>
        </li>
        <li>
          <svg viewBox="0 0 12 12" aria-hidden="true"><circle cx="6" cy="6" r="5" fill="none" stroke="#fff" stroke-width="1"/><ellipse cx="6" cy="6" rx="2.2" ry="5" fill="none" stroke="#fff" stroke-width="0.9"/><path d="M1 6 H11" stroke="#fff" stroke-width="0.9"/></svg>
          <span>www.brenoloft.com</span>
        </li>
      </ul>
    </div>
  </section>

  <section class="card card-back" aria-label="Business card back">
    <div class="wordmark">brenoloft</div>
    <p class="follow">Follow Us On: <span class="social-dot" aria-hidden="true"></span><span class="social-dot" aria-hidden="true"></span></p>
    <p class="web">www.brenoloft.com</p>
  </section>
</main>
</body>
</html>
```